Shipping Container Sales & Leasing Flyer

We need a flyer that is going to be presented and left behind while prospecting potential customers. The service we are selling is the sale, rental and customization of 20' and 40' shipping containers.

We provide new and used containers to customers for various reasons, mainly storage. We also custom modify containers into storage units, mobile offices, mobile job site storage, command centers, pump houses, garages, living space, the only limit is the customers imagination.

I would like our company logo and phone / email at the bottom but the design should showcase some of the attached images ive provided as examples and have spots where we can list the types of equipment we have for sale and the various types of conversions we can offer.

Please also tie in to the colour scheme of our logo.

Target Market(s)

Moving & Storage, Construction, Contractors, Business to Business, Any business that needs portable storage, Landscapers, Property Maintenance companies.

Industry/Entity Type

Shipping

Font styles to use
Serif
Sans Serif

Requirements
Must have
• Professional feel, clean original design.
Nice to have
• Tie in to our logo colour scheme.
Should not have
• Bulky or crowded look

```html
<!DOCTYPE html>
<html lang="en">
<head>
<meta charset="utf-8">
<title>Tarrow Management – Shipping Container Flyer</title>
<link rel="stylesheet" href="https://fonts.googleapis.com/css2?family=Roboto+Condensed:wght@700&family=Lato:ital,wght@0,400;1,700&family=Montserrat:wght@500;700&display=swap">
<style>
:root{
  --green:#5e9b3a;
  --green-light:#7cb24e;
  --green-dark:#3f7424;
  --ink:#121212;
  --band-dark:#0e0e0e;
  --band-mid:#4a4a4a;
  --paper:#ffffff;
  --stage:#ececec;
  --steel:#8d9296;
}
*{margin:0;padding:0;box-sizing:border-box}
html,body{width:907px;height:1200px;overflow:hidden;background:var(--stage)}
.flyer{position:absolute;left:83px;top:88px;width:729px;height:1020px;background:var(--paper);overflow:hidden;box-shadow:0 4px 14px rgba(0,0,0,.18)}
.flyer-shapes{position:absolute;inset:0}
.brand{position:absolute;left:0;top:150px;width:297px;text-align:center;font-family:"Montserrat",sans-serif}
.brand-mark{width:58px;height:58px;border-radius:50%;background:var(--green);margin:0 auto 16px}
.brand-name{font-weight:700;font-size:40px;letter-spacing:6px;color:var(--green);line-height:1}
.brand-sub{font-weight:500;font-size:11px;letter-spacing:5px;color:#333;margin-top:6px}
.photo{position:absolute}
.photo-storage{left:305px;top:0;width:424px;height:312px;background:linear-gradient(180deg,#e4e6e8 0%,#c9cbcc 45%,#9a9a98 100%)}
.photo-container{left:387px;top:692px;width:342px;height:282px;background:linear-gradient(160deg,#a7abae 0%,#8b9094 55%,#70757a 100%);clip-path:polygon(0 10%,70% 0,100% 4%,100% 96%,70% 100%,0 90%)}
.headline{position:absolute;left:0;width:729px;text-align:center;font-family:"Roboto Condensed",sans-serif;font-weight:700;text-transform:uppercase}
.headline-kicker{top:418px;font-family:"Montserrat",sans-serif;font-weight:500;font-size:22px;letter-spacing:1px;color:var(--green-light)}
.headline-main{top:444px;font-size:38px;color:#fff}
.modify-label{position:absolute;left:33px;top:534px;font-family:"Roboto Condensed",sans-serif;font-weight:700;font-size:23px;line-height:31px;color:#fff}
.uses{position:absolute;list-style:none;font-family:"Lato",sans-serif;font-style:italic;font-weight:700;font-size:16px;color:var(--ink)}
.uses li{position:relative;padding-left:21px;height:27.5px;line-height:20px}
.uses li::before{content:"";position:absolute;left:0;top:5px;width:11px;height:11px;border-radius:50%;border:2px solid var(--green)}
.uses-left{left:30px;top:620px}
.uses-right{left:244px;top:618px}
.call{position:absolute;left:30px;top:775px;font-family:"Roboto Condensed",sans-serif;font-weight:700}
.call-title{font-size:62px;line-height:1;color:var(--ink)}
.call-phone{font-size:52px;line-height:1;color:var(--green);margin-top:8px;letter-spacing:1px}
.contact{position:absolute;left:28px;top:952px;list-style:none;font-family:"Lato",sans-serif;font-size:16px;color:#fff}
.contact li{display:flex;align-items:center;gap:8px;height:28px}
.contact svg{width:20px;height:16px}
</style>
</head>
<body>
<main class="flyer">
  <svg class="flyer-shapes" width="729" height="1020" viewBox="0 0 729 1020" aria-hidden="true">
    <defs>
      <linearGradient id="panelGrad" x1="0" y1="0" x2="1" y2="0">
        <stop offset="0" stop-color="#d9d9d9"/><stop offset=".5" stop-color="#f7f7f7"/><stop offset="1" stop-color="#dcdcdc"/>
      </linearGradient>
      <linearGradient id="bandGrad" x1="0" y1="0" x2="1" y2="0">
        <stop offset="0" stop-color="#0e0e0e"/><stop offset=".55" stop-color="#2a2a2a"/><stop offset="1" stop-color="#5a5a5a"/>
      </linearGradient>
      <linearGradient id="labelGrad" x1="0" y1="0" x2="1" y2="0">
        <stop offset="0" stop-color="#3f7424"/><stop offset="1" stop-color="#6fa844"/>
      </linearGradient>
    </defs>
    <polygon points="0,0 297,0 297,362 149,297 0,355" fill="url(#panelGrad)"/>
    <polyline points="0,355 149,297 297,362" fill="none" stroke="#5e9b3a" stroke-width="6"/>
    <line x1="298" y1="0" x2="298" y2="368" stroke="#5e9b3a" stroke-width="4"/>
    <rect x="305" y="320" width="424" height="6" fill="#5e9b3a"/>
    <rect x="0" y="384" width="729" height="128" fill="url(#bandGrad)"/>
    <polygon points="462,512 729,512 729,925 380,925 572,652" fill="#5e9b3a"/>
    <polyline points="462,512 572,652 380,925" fill="none" stroke="#e6e6e6" stroke-width="3"/>
    <polygon points="0,525 385,525 310,600 0,600" fill="url(#labelGrad)"/>
    <rect x="0" y="924" width="729" height="5" fill="#5e9b3a"/>
    <rect x="0" y="934" width="729" height="86" fill="url(#bandGrad)"/>
  </svg>

  <div class="photo photo-storage" role="img" aria-label="Photo of a shipping container converted into storage units with orange roll-up doors"></div>
  <div class="photo photo-container" role="img" aria-label="Photo of a grey 20 foot shipping container"></div>

  <header class="brand">
    <div class="brand-mark"></div>
    <div class="brand-name">TARROW</div>
    <div class="brand-sub">MANAGEMENT</div>
  </header>

  <h1 class="headline headline-kicker">Sales and rental of new and used</h1>
  <h2 class="headline headline-main">10', 20' and 40' shipping containers</h2>

  <p class="modify-label">We also custom modify<br>containers!</p>

  <ul class="uses uses-left">
    <li>Storage units</li>
    <li>Mobile offices</li>
    <li>Mobile job site storage</li>
    <li>Command centers</li>
    <li>Pump houses</li>
  </ul>
  <ul class="uses uses-right">
    <li>Garages</li>
    <li>living space</li>
    <li>The only limit is<br>the customers imagination</li>
  </ul>

  <section class="call">
    <div class="call-title">CALL NOW</div>
    <div class="call-phone">0198765432</div>
  </section>

  <ul class="contact">
    <li><svg viewBox="0 0 20 16"><rect x="1" y="2" width="18" height="12" fill="none" stroke="#7cb24e" stroke-width="1.5"/><polyline points="1,2 10,9 19,2" fill="none" stroke="#7cb24e" stroke-width="1.5"/></svg>hello@tarrowboxes.com</li>
    <li><svg viewBox="0 0 20 16"><circle cx="10" cy="8" r="7" fill="none" stroke="#7cb24e" stroke-width="1.5"/><line x1="3" y1="8" x2="17" y2="8" stroke="#7cb24e" stroke-width="1.2"/><ellipse cx="10" cy="8" rx="3" ry="7" fill="none" stroke="#7cb24e" stroke-width="1.2"/></svg>www.tarrowboxes.com</li>
  </ul>
</main>
</body>
</html>
```